Kesso Tea Premium Matcha brand Label

This is a label design project for a luxury tea brand. Feel free to be creative within the guidelines.
Attached to this project is a document called “Private Label Design Requirements” with the design guidelines and template. There is another document called "Kesso Tea Packaging Instructions" this has more details necessary to stick to the guidelines in the first document.

I have also attached the certifications to be included as well as different variations of the logo for you to use.

If you have any questions, I am here.
Updates

Need extra days to review

Target Market(s)

Young, active, fun, enjoy the finer things

```html
<!DOCTYPE html>
<html lang="en">
<head>
<meta charset="utf-8">
<title>Kesso Tea Premium Matcha Label</title>
<link rel="stylesheet" href="https://fonts.googleapis.com/css2?family=Marcellus&family=Open+Sans:wght@400;600&family=Josefin+Sans:wght@400&display=swap">
<style>
  :root {
    --backdrop: #e4e6e5;
    --label-cream: #ece6d3;
    --leaf-green: #9cc77a;
    --leaf-green-soft: #c3dcae;
    --ink: #2f2e2a;
    --ink-soft: #4a4842;
    --brown: #6d5b44;
    --gold: #c4a968;
    --badge-blue: #2d6c8c;
    --badge-green: #4f8a3c;
  }
  * { box-sizing: border-box; margin: 0; padding: 0; }
  html, body { width: 1088px; height: 1200px; overflow: hidden; }
  body {
    background: var(--backdrop);
    font-family: "Open Sans", sans-serif;
    color: var(--ink);
    position: relative;
  }
  .label {
    position: absolute;
    left: 30px;
    top: 420px;
    width: 1028px;
    height: 360px;
    background: var(--label-cream);
    display: grid;
    grid-template-columns: 239px 110px 330px 110px 239px;
    border-bottom: 14px solid var(--gold);
  }
  .panel { position: relative; padding: 56px 24px 0; }
  .leaf-cluster {
    margin: 40px 6px;
    border-radius: 50%;
    background: radial-gradient(ellipse at center, var(--leaf-green) 0%, var(--leaf-green-soft) 60%, var(--label-cream) 100%);
  }

  .distributor-panel { padding-top: 120px; font-size: 11px; line-height: 1.55; color: var(--ink-soft); }
  .distributor-panel .line-strong { font-weight: 600; }
  .cert-badges { display: flex; gap: 10px; margin-top: 18px; }
  .cert-badge-square { width: 34px; height: 34px; background: var(--badge-blue); }
  .cert-badge-circle { width: 34px; height: 34px; border-radius: 50%; border: 3px solid var(--badge-green); background: #fff; }

  .front-panel { text-align: center; padding-top: 42px; }
  .brand-mark { display: inline-flex; align-items: center; gap: 8px; }
  .brand-mark-square { width: 22px; height: 22px; background: var(--ink); }
  .brand-name { font-family: "Open Sans", sans-serif; font-weight: 600; font-size: 17px; color: var(--ink); }
  .product-subtitle {
    margin-top: 46px;
    display: flex; align-items: center; justify-content: center; gap: 8px;
    font-family: "Josefin Sans", sans-serif; font-size: 17px; color: var(--brown); letter-spacing: 0.5px;
  }
  .product-subtitle .rule { width: 26px; height: 1.5px; background: var(--brown); }
  .product-title {
    font-family: "Marcellus", serif; font-size: 70px; line-height: 1; letter-spacing: 1px;
    color: var(--ink); margin-top: 2px;
  }
  .net-weight { font-size: 13px; font-weight: 600; color: var(--ink-soft); margin-top: 8px; }

  .ingredients-panel { padding-top: 70px; color: var(--ink-soft); }
  .ingredients-heading { font-size: 15px; font-weight: 600; color: #6c6a63; }
  .ingredients-list { font-size: 15px; line-height: 1.25; margin-top: 4px; }
  .divider { width: 56px; height: 1px; background: var(--ink-soft); margin: 18px 0; }
  .directions { list-style: none; font-size: 12.5px; line-height: 1.6; }
  .directions li::before { content: "•"; margin-right: 7px; }
</style>
</head>
<body>
  <div class="label">
    <section class="panel distributor-panel">
      <p>Distributed by Kesso Tea Co. | Lakemont, Ga</p>
      <p class="line-strong">Certified Organic by Verda</p>
      <p>PRODUCT OF JAPAN</p>
      <div class="cert-badges">
        <div class="cert-badge-square" role="img" aria-label="Non-GMO certification badge"></div>
        <div class="cert-badge-circle" role="img" aria-label="Organic certification badge"></div>
      </div>
    </section>

    <div class="leaf-cluster" role="img" aria-label="Decorative cluster of green tea leaves"></div>

    <section class="panel front-panel">
      <div class="brand-mark">
        <span class="brand-mark-square"></span>
        <span class="brand-name">Kesso Tea</span>
      </div>
      <p class="product-subtitle"><span class="rule"></span>Premium Organic Ceremonial<span class="rule"></span></p>
      <h1 class="product-title">MATCHA</h1>
      <p class="net-weight">Net Wt: 30g (1.06oz)</p>
    </section>

    <div class="leaf-cluster" role="img" aria-label="Decorative cluster of green tea leaves"></div>

    <section class="panel ingredients-panel">
      <h2 class="ingredients-heading">Ingredients</h2>
      <p class="ingredients-list">Premium Organic Japanese Matcha Green Tea</p>
      <div class="divider"></div>
      <ul class="directions">
        <li>2 tsp of Matcha</li>
        <li>2oz of Water (170-180 degrees F)</li>
        <li>Whisk in a W formation until frothy</li>
        <li>Sweeten to taste</li>
      </ul>
    </section>
  </div>
</body>
</html>
```